RaymondOsgood

I will be video blogging 1 - 5 minute instructional videos about all kind or stuff

I want it took look clean.
I have secured Raymondosgood.com
Do you design vidmora pages as well.
I will upload to vidmora and correspond with websites.
Website wil include
videos with longer written description
how to book me.
where I am speaking at next
Thank you

Reason: my design is going to be more detailed than i had expected

Reason: still have changes

Vidmora

```html
<!DOCTYPE html>
<html lang="en">
<head>
<meta charset="utf-8">
<title>raymondosgood.com</title>
<link rel="stylesheet" href="https://fonts.googleapis.com/css2?family=Open+Sans:wght@400;600;700&display=swap">
<style>
:root{
  --page-outer:#2e1a06;
  --page-mid:#5a3408;
  --column:#3b2106;
  --blue:#1aa6ec;
  --blue-dark:#0f8fd2;
  --white:#ffffff;
  --panel:#f0f0f0;
  --text:#4a4a4a;
  --heading:#111111;
  --date:#e52222;
  --video:#141414;
  --rule:#e2e2e2;
  --bar:#b8b8b8;
}
*{margin:0;padding:0;box-sizing:border-box}
html,body{width:1200px;height:1000px;overflow:hidden}
body{font-family:"Open Sans",Arial,sans-serif;background:radial-gradient(ellipse at 50% 10%,var(--page-mid),var(--page-outer) 75%);position:relative}
.site-column{position:absolute;left:156px;top:0;width:886px;height:1000px;background:linear-gradient(180deg,#4d2c06 0%,var(--column) 100%)}
.site-name{position:absolute;left:295px;top:20px;font-size:24px;font-weight:700;color:var(--white);letter-spacing:-.3px}
.hero-photo{position:absolute;left:287px;top:62px;width:400px;height:150px;background:linear-gradient(90deg,#9c9a45 0%,#c9c48a 35%,#efe6cf 60%,#d9cdb4 100%)}
.featured{position:absolute;left:687px;top:62px;width:230px;height:150px;background:var(--video)}
.panel-head{background:var(--blue);color:var(--white);font-size:10px;font-weight:700;text-align:center;text-transform:uppercase;height:22px;line-height:22px}
.video-still{position:absolute;background:linear-gradient(135deg,#262626,#0d0d0d)}
.play{position:absolute;display:flex;align-items:center;gap:6px;color:var(--white);text-transform:uppercase;white-space:nowrap}
.play svg{display:block}
.controls{position:absolute;left:0;right:0;bottom:0;height:18px;background:#0a0a0a;border-top:2px solid #3a0a0a}
.nav{position:absolute;left:287px;top:212px;width:630px;height:35px;background:var(--blue)}
.nav ul{list-style:none;display:flex;gap:10px;position:absolute;left:8px;top:10px}
.nav a{color:var(--white);font-size:11px;font-weight:600;text-decoration:none}
.nav .pointer{position:absolute;left:8px;top:34px}
.search{position:absolute;left:436px;top:7px;width:135px;height:22px;background:var(--white);border-radius:3px;font-size:9px;color:#aaa;padding:4px 8px}
.search svg{position:absolute;right:5px;top:4px}
.search i{position:absolute;right:25px;top:3px;width:1px;height:16px;background:#999}
.social{position:absolute;top:8px;width:19px;height:19px;border-radius:50%;background:var(--white);border:2px solid #5c90d2}
.content{position:absolute;left:287px;top:247px;width:630px;height:753px;background:var(--white)}
.post-title{position:absolute;font-size:19px;font-weight:400;color:var(--heading)}
.post-video{position:absolute;width:373px;height:232px;border:4px solid var(--blue);border-radius:4px;background:var(--video);overflow:hidden}
.posted{position:absolute;left:10px;top:288px;font-size:10px;color:#666}
.posted span{color:var(--date)}
.post-body{position:absolute;left:10px;top:308px;width:364px;font-size:10.2px;line-height:10.7px;color:var(--text)}
.post-body p{margin-bottom:10px}
.divider{position:absolute;left:10px;top:678px;width:360px;height:1px;background:var(--rule)}
.side-box{position:absolute;left:441px;width:179px;background:var(--panel);border:1px solid var(--blue);border-radius:4px;overflow:hidden}
.side-box .panel-head{height:24px;line-height:24px}
.recent-item{position:absolute;left:7px;display:flex;gap:9px}
.thumb{position:relative;width:83px;height:48px;border:2px solid var(--blue);background:linear-gradient(135deg,#2a2a2a,#0e0e0e)}
.thumb .play{left:10px;top:14px;font-size:7px;font-weight:600}
.thumb b{position:absolute;right:3px;bottom:1px;font-size:6px;color:#ccc;font-weight:400}
.recent-item p{font-size:9.5px;line-height:11px;color:var(--heading);width:70px;font-weight:600;margin-top:1px}
.more{position:absolute;left:44px;top:209px;width:87px;height:17px;background:var(--blue);border-radius:3px;color:var(--white);font-size:9px;font-weight:700;text-align:center;line-height:17px}
.side-bar{position:absolute;left:442px;top:269px;width:174px;height:6px;background:var(--bar)}
</style>
</head>
<body>
<div class="site-column"></div>
<div class="site-name">raymondosgood.com</div>

<div class="hero-photo" role="img" aria-label="Portrait of Raymond Osgood in a suit before a faded word cloud about instruction and feedback"></div>

<section class="featured">
  <div class="panel-head">Featured Video</div>
  <div class="video-still" role="img" aria-label="Featured video still" style="left:0;top:22px;width:230px;height:128px"></div>
  <div class="play" style="left:54px;top:58px;font-size:15px">
    <svg width="32" height="32" viewBox="0 0 32 32"><circle cx="16" cy="16" r="14" fill="none" stroke="#fff" stroke-width="3"/><path d="M12.5 9.5 L23 16 L12.5 22.5Z" fill="#fff"/></svg>PLAY NOW!
  </div>
  <div class="controls" style="height:20px"></div>
</section>

<nav class="nav">
  <ul><li><a href="#">Home</a></li><li><a href="#">Videos</a></li><li><a href="#">Discussion</a></li><li><a href="#">About</a></li></ul>
  <svg class="pointer" width="12" height="7" viewBox="0 0 12 7"><path d="M0 0 H12 L6 7Z" fill="#1aa6ec"/></svg>
  <div class="search">search<i></i>
    <svg width="14" height="14" viewBox="0 0 14 14"><circle cx="5.5" cy="5.5" r="4" fill="none" stroke="#555" stroke-width="1.6"/><path d="M8.5 8.5 L13 13" stroke="#555" stroke-width="2"/></svg>
  </div>
  <span class="social" style="left:579px" aria-label="Social link"></span>
  <span class="social" style="left:603px" aria-label="Social link"></span>
</nav>

<main class="content">
  <h2 class="post-title" style="left:7px;top:12px">How to make video 1</h2>
  <div class="post-video" style="left:8px;top:43px">
    <div class="video-still" role="img" aria-label="Video still of hands working on a wooden board at a workbench" style="left:0;top:0;width:100%;height:100%"></div>
    <div class="play" style="left:122px;top:96px;font-size:14px">
      <svg width="30" height="30" viewBox="0 0 32 32"><circle cx="16" cy="16" r="14" fill="none" stroke="#fff" stroke-width="3"/><path d="M12.5 9.5 L23 16 L12.5 22.5Z" fill="#fff"/></svg>PLAY NOW!
    </div>
    <div class="controls"></div>
  </div>
  <p class="posted">Posted: <span>June 2, 2014</span></p>
  <div class="post-body">
    <p>Lorem ipsum dolor sit amet, consectetur adipiscing elit. Fusce lobortis mauris id augue tempus volutpat eget quis dui. Pellentesque quis molestie enim, quis pretium lorem. Ut vitae scelerisque purus. Sed commodo augue a faucibus congue. Ut purus urna, sagittis non neque vel, mollis ullamcorper justo. Etiam quis dui tristique, iaculis turpis et, euismod leo. Mauris vulputate suscipit dictum. Morbi consequat lacinia vestibulum. Cum sociis natoque penatibus et magnis dis parturient montes, nascetur ridiculus mus. Duis euismod mauris elementum, imperdiet nisi eget, mollis turpis. Phasellus eleifend enim vulputate tincidunt convallis. Donec fringilla augue sapien, a mollis quam blandit nec.</p>
    <p>Phasellus varius lacinia eleifend. Sed id gravida diam, sed convallis nibh. Praesent sed odio in leo volutpat imperdiet et luctus tortor. Ut ullamcorper interdum sapien, vitae vulputate dui tristique vel. Sed nec tellus a eros malesuada malesuada. Duis elementum sagittis leo, quis congue est vehicula non. Integer at ullamcorper erat. Duis sodales dui nec interdum egestas. Sed rutrum diam orci, id egestas mi suscipit at. Fusce convallis sed neque ut bibendum. Nunc vitae libero vulputate, tristique quam id, viverra eros.</p>
    <p>Duis suscipit interdum magna, sit amet dignissim enim convallis et. Praesent lorem nunc, pulvinar eget odio at, feugiat placerat nisl. Integer et tellus purus. Praesent ac arcu sed ante elementum tincidunt. Suspendisse vitae lorem porttitor, aliquam ante sit amet, adipiscing urna. Praesent non nibh volutpat nunc lobortis pellentesque ac vitae quam. Nulla sed tellus a dui consequat tincidunt. Praesent et tempus massa, ac ullamcorper tortor. Integer sollicitudin posuere risus nec tempor. Proin at interdum nulla. Nulla in urna a nisi facilisis pretium quis condimentum felis. Aenean eleifend ut dolor ac cursus. Curabitur lobortis quis ante euismod suscipit. Suspendisse congue, nibh vitae interdum consequat, tortor nulla ornare urna, a accumsan dui leo quis erat. Donec sit amet neque a nulla ullamcorper aliquet. Nunc.</p>
  </div>
  <div class="divider"></div>
  <h2 class="post-title" style="left:10px;top:688px">How to make video 2</h2>
  <div class="post-video" style="left:11px;top:719px">
    <div class="video-still" role="img" aria-label="Video still for video 2" style="left:0;top:0;width:100%;height:100%"></div>
  </div>

  <aside class="side-box" style="top:18px;height:234px">
    <div class="panel-head">Recent Videos</div>
    <div class="recent-item" style="top:36px"><div class="thumb" role="img" aria-label="Thumbnail for video 1"><span class="play"><svg width="14" height="14" viewBox="0 0 32 32"><circle cx="16" cy="16" r="13" fill="none" stroke="#fff" stroke-width="4"/><path d="M12.5 9.5 L23 16 L12.5 22.5Z" fill="#fff"/></svg>PLAY NOW!</span><b>7:10</b></div><p>How to make a video 1</p></div>
    <div class="recent-item" style="top:92px"><div class="thumb" role="img" aria-label="Thumbnail for video 2"><span class="play"><svg width="14" height="14" viewBox="0 0 32 32"><circle cx="16" cy="16" r="13" fill="none" stroke="#fff" stroke-width="4"/><path d="M12.5 9.5 L23 16 L12.5 22.5Z" fill="#fff"/></svg>PLAY NOW!</span><b>5:20</b></div><p>How to make a video 2</p></div>
    <div class="recent-item" style="top:149px"><div class="thumb" role="img" aria-label="Thumbnail for video 3"><span class="play"><svg width="14" height="14" viewBox="0 0 32 32"><circle cx="16" cy="16" r="13" fill="none" stroke="#fff" stroke-width="4"/><path d="M12.5 9.5 L23 16 L12.5 22.5Z" fill="#fff"/></svg>PLAY NOW!</span><b>5:08</b></div><p>How to make a video 3</p></div>
    <a class="more">SEE MORE VIDEOS</a>
  </aside>
  <div class="side-bar"></div>
  <aside class="side-box" style="top:289px;height:234px">
    <div class="panel-head">Video Archives</div>
  </aside>
</main>
</body>
</html>
```